Edgey, Modern Air Conditioning Website

Bramble Works
current website - www.kelvaroom.nz
Friendwall - www.facebook.com/bramwrk

We really have no idea about webdesign etc we are Engineers not Graphic artists or creative writers. We really just want a edgy, modern website completed on our behalf

We can get pictures of projects as directed or happy for you to use stock images of Talvoro Mecha NZ (Heatpumps) air conditioning and exposed ducting etc

we would like the website to be heavily based on the below website. I like what they have done with both the site and the app but obviously would need to suit Bramble Works, snowflakes heating cooling etc etc Blue and white to match our logo etc

http://parrowbeams.co.nz/

Need links to contact page:
Bramble Works
27 Harlow Crescent
Petone
Wellington

0800 529 174 (0800BRAMWKS)

Marta.k@bramwks.co.nz

BRAMBLE WORKS
SATISFACTION GAURANTEED

WHY CHOOSE BRAMBLE WORKS
EXPERIENCE COUNTS

We have a team of nationally trained and qualified Refrigeration/HVAC/Electrical Engineers and Technicians based in Petone, Wellington offering services to Wellington, Manuwatu and the Wairarapa. We are factory trained and authorised to design, service and install all major brands including Talvoro, Pelnor, Korrowane Electric, Veltrada and Osmelo units. We extend our installation warranty to match that of the manufacturer’s warranty and specialise in our own diagnostics and repair.

SATISFACTION GUARANTEE
We aim to please and I put my name behind our brand! We will take care of your project from start to finish and offer a unique experience with our 100% satisfaction Guarantee*. We will supply and install your system and if your system is not installed how it was explained or not up to a trades standard we will return to make any the necessary modifications free of charge. We back this service up with our 0% upfront strategy, the power is in your hands. We will only invoice you once the installation has been completed up to a BRAMBLE WORKS standard.

LOW PRESSURE SALES
Nobody likes the vacuum salesmen’s techniques and neither do we. We will come to your home or business to provide a free measure and quote. Our experience will insure this is a quick and painless experience, you will be provided with expert advice from a qualified Refrigeration Engineer, not a car salesmen turned “Heating Guru”. We will follow up with an email providing our best price straight up, installation details and online brochures. We won’t bug you with repeated phone calls and inbox clogging emails. Once we receive confirmation we will issue you with an installation date and typically have your installation completed within 10 working days.

BRANDS
www.talvoromecha.co.nz
www.pelnor.co.nz
http://quellaro.co.nz/

SERVICES
Heatpumps/Air Conditioning – Heat pumps are the most efficient way of using electricity to heat your home, but some are more efficient than others. We will select the right model for your requirements taking into account the capacity required, the visual impact of the system, the style of system, air flow and obviously your personal preferences. We only install the highest quality brands that offer outstanding after sales support. Cassettes, Consoles, Under Ceilings, Ducted, Hiwalls, Multis… Confused? Give us a call.

COMMERCIAL
We have a growing Portfolio of clients that rely on us for their Commercial requirements. We have proven ourselves to be a force to be reckoned with to be able to think outside the square and come up with unique and cost effective solutions to heat and cool large areas.

CENTRAL HEATING
Ducted Heatpumps are the holy grail of central heating and guess what? They can also cool and dehumidify your home. Ducted Heatpumps are often overlooked or priced out of reach by less experienced salesmen as its not just a point and shoot approach. We pride ourselves in our work with Ducted systems, we are able to provide quick and economic quotations and can provide expert advice on all the extra options on Ducted systems with zone control, fresh air integration, positive pressure solutions. We use the best materials when it comes to insulated ducting, mounting equipment, drainage materials. Every system we design is designed with the lowest possible decibel reading, least amount of static pressure and maximum effieciency with the help of the very latest software available.

VENTILATION
Home ventilation is a very important part of insuring you have a nice dry home to maximise the efficiency of your Heat pump. Whilst HRV systems are not designed to Heat your house they are designed to keep it dry, provide fresh filtered air to ensure your home healthy and easy to heat. We offer a number of solutions from integrated ducted heatpump systems to balanced heat recovery systems and positive air systems.

TESTIMONIALS
http://www.lotbazaro.co.nz/Browse/Listing.aspx?id=415728306

Target Market(s)

Home Owners

Industry/Entity Type

Air Conditioning

Colors
33a6d7
ffffff

Requirements
Must have
• Could possibly use the 'O' from Bramble Works logo throughout website - see business Card
Nice to have
• Bright & Crisp - White and Blue
• Would love to have our Logo used throughout the website.

```html
<!DOCTYPE html>
<html lang="en">
<head>
<meta charset="utf-8">
<title>Bramble Works – Heating, Cooling &amp; Ventilation</title>
<link href="https://fonts.googleapis.com/css2?family=Raleway:ital,wght@0,400;0,500;0,600;0,700;0,800;1,400&family=Open+Sans:wght@400;600;700&display=swap" rel="stylesheet">
<style>
:root{
  --blue:#33a6d7;
  --blue-deep:#2a83b5;
  --navy:#22364a;
  --navy-dark:#1b2c3c;
  --ink:#1f1f1f;
  --text:#555;
  --muted:#8a8a8a;
  --line:#dcdcdc;
  --soft:#f5f5f5;
  --white:#fff;
}
*{box-sizing:border-box;margin:0;padding:0}
html,body{width:1200px;height:2922px;overflow:hidden}
body{position:relative;background:var(--white);font-family:"Raleway",sans-serif;color:var(--text)}
.abs{position:absolute}

/* header */
.brand{left:82px;top:30px;display:flex;align-items:center;gap:12px}
.brand-dot{width:34px;height:34px;border-radius:50%;background:var(--blue)}
.brand-name{font-family:"Raleway",sans-serif;font-weight:800;font-size:36px;letter-spacing:2px;color:var(--blue)}
.top-contact{top:18px;display:flex;align-items:center;gap:10px;font-family:"Open Sans",sans-serif;font-size:17px;color:var(--ink)}
.round-icon{width:34px;height:34px;border-radius:50%;background:var(--blue);display:flex;align-items:center;justify-content:center}
.nav-rule{left:483px;top:66px;width:717px;height:1px;background:var(--line)}
.nav{top:84px;left:0;width:1200px;font-family:"Raleway",sans-serif;font-weight:700;font-size:15px;color:var(--ink);letter-spacing:.3px}
.nav a{position:absolute;color:inherit;text-decoration:none}
.nav a.active{color:var(--blue)}

/* hero */
.hero{left:0;top:119px;width:1200px;height:525px;background:linear-gradient(120deg,#d9cfc2 0%,#b8a48e 35%,#8e8272 60%,#d8d4cc 100%)}
.hero-caption{left:0;top:594px;width:1200px;height:50px;background:rgba(0,0,0,.45);color:var(--white);font-family:"Open Sans",sans-serif;font-weight:700;font-size:24px;line-height:50px;text-align:center}
.hero-arrow{top:340px}

/* section titles */
.section-title{left:0;width:1200px;text-align:center;font-weight:700;font-size:27px;color:var(--ink);letter-spacing:.5px}
.section-title span{color:var(--blue)}
.divider{left:343px;width:514px;height:24px}
.divider::before{content:"";position:absolute;left:0;right:0;top:11px;height:2px;background:var(--line)}
.divider::after{content:"";position:absolute;left:246px;top:1px;width:22px;height:22px;border-radius:50%;background:var(--white);border:3px solid #c9c9c9}

.welcome-copy{left:80px;top:786px;width:1040px;text-align:center;font-size:13.5px;line-height:23px;color:var(--text)}
.btn{display:inline-flex;align-items:center;justify-content:center;gap:6px;font-weight:700;font-size:13px;text-decoration:none}
.btn-primary{left:538px;top:919px;width:125px;height:38px;background:var(--blue);color:var(--white)}

/* services */
.services{left:0;top:1009px;width:1200px;height:413px;background:var(--blue)}
.service{position:absolute;top:0;height:413px;text-align:center;color:var(--white)}
.service-bg{position:absolute;inset:0}
.service.light .service-bg{background:linear-gradient(160deg,#48b3e0,#2f9ccd)}
.service.dark .service-bg{background:linear-gradient(160deg,#2d4357,#1f3141);clip-path:polygon(0 26px,26px 0,calc(100% - 26px) 0,100% 26px,100% calc(100% - 26px),calc(100% - 26px) 100%,26px 100%,0 calc(100% - 26px))}
.service-icon{position:absolute;left:50%;top:44px;margin-left:-58px;width:116px;height:116px;border-radius:50%;background:var(--white);display:flex;align-items:center;justify-content:center}
.service h3{position:absolute;left:0;right:0;top:190px;font-size:21px;font-weight:700;letter-spacing:.5px}
.service p{position:absolute;left:50%;top:234px;width:220px;margin-left:-110px;height:92px;overflow:hidden;font-family:"Open Sans",sans-serif;font-size:13.5px;font-weight:600;line-height:23px}
.btn-card{position:absolute;left:50%;top:1343px;margin-left:-58px;width:116px;height:34px;background:var(--white);color:var(--blue-deep);font-size:13px}
.service .btn-card{top:334px}

/* gallery */
.gallery-item{top:1574px;width:251px;height:176px}

/* testimonials + why */
.band-soft{left:0;top:1808px;width:1200px;height:432px;background:var(--soft)}
.col-title{top:1851px;font-weight:700;font-size:27px;color:var(--ink)}
.col-title span{color:var(--blue)}
.col-rule{top:1904px;height:1px;background:var(--line)}
.v-dash{left:598px;top:1858px;width:0;height:340px;border-left:2px dashed #d2d2d2}
.avatar{left:78px;top:1939px;width:116px;height:116px;border-radius:50%;border:4px solid var(--white);box-shadow:0 0 0 2px var(--blue);background:linear-gradient(160deg,#cfd6dc,#8d99a3)}
.quote-mark{left:224px;top:1906px;font-family:"Open Sans",sans-serif;font-size:72px;color:#cdcdcd;line-height:1}
.quote{left:228px;top:1928px;width:340px;font-style:italic;font-size:16.5px;line-height:28.5px;color:#333}
.client-name{left:228px;top:2117px;font-family:"Open Sans",sans-serif;font-weight:600;font-size:19px;color:var(--blue)}
.client-role{left:228px;top:2148px;font-family:"Open Sans",sans-serif;font-size:13px;color:#333}

.why-line{left:682px;top:1958px;width:0;height:190px;border-left:2px dashed #bdbdbd}
.why-icon{left:647px;width:70px;height:70px;border-radius:50%;background:var(--blue);border:4px solid var(--white);box-shadow:0 0 0 2px var(--blue);display:flex;align-items:center;justify-content:center}
.why-item{left:744px;width:380px}
.why-item h4{font-family:"Open Sans",sans-serif;font-weight:700;font-size:15.5px;color:var(--ink);margin-bottom:8px}
.why-item p{font-family:"Open Sans",sans-serif;font-size:13px;line-height:22px;color:var(--text)}
.why-item p a{color:var(--blue);text-decoration:none}
.why-sep{left:744px;width:378px;height:1px;background:var(--line)}

/* brands */
.brand-tile{top:2396px;width:150px;height:70px;border:1px solid #ddd;background:var(--white);display:flex;align-items:center;justify-content:center;font-family:"Raleway",sans-serif;font-weight:800;font-size:19px;color:#333}
.brand-arrow{top:2417px}

/* newsletter */
.newsletter{left:0;top:2513px;width:1200px;height:78px;background:var(--blue-deep)}
.news-icon{left:112px;top:2525px;width:54px;height:54px;border-radius:50%;border:2px solid var(--white);display:flex;align-items:center;justify-content:center}
.news-title{left:193px;top:2534px;font-weight:700;font-size:27px;color:var(--white)}
.news-input{left:493px;top:2533px;width:384px;height:38px;background:var(--white);font-family:"Open Sans",sans-serif;font-size:13px;color:#333;padding:0 10px;line-height:38px}
.news-btn{left:892px;top:2533px;width:193px;height:38px;background:var(--navy);color:var(--white);font-family:"Open Sans",sans-serif;font-weight:700;font-size:17px;letter-spacing:1.5px}

/* footer */
.footer{left:0;top:2591px;width:1200px;height:284px;background:linear-gradient(180deg,#24394e,#1c2e40)}
.foot-title{top:2630px;font-family:"Open Sans",sans-serif;font-weight:700;font-size:16px;color:var(--white);letter-spacing:.5px}
.foot-title span{color:var(--blue)}
.foot-rule{top:2660px;width:125px;height:1px;background:rgba(255,255,255,.25)}
.foot-links{left:82px;top:2680px;list-style:none;font-family:"Open Sans",sans-serif;font-size:13.5px;color:#c9d3dc}
.foot-links li{height:31px;padding-left:14px;position:relative}
.foot-links li::before{content:"›";position:absolute;left:0;color:var(--blue)}
.foot-links li.current{color:var(--white);font-weight:700}
.foot-contact{left:321px;top:2680px;font-family:"Open Sans",sans-serif;font-size:13.5px;color:#c9d3dc;line-height:23px}
.foot-contact strong{color:var(--white);font-weight:700}
.foot-row{display:flex;align-items:center;gap:10px;margin-top:13px}
.field{left:666px;width:228px;height:29px;background:var(--white);font-family:"Open Sans",sans-serif;font-size:12px;color:#999;padding:0 8px;line-height:29px}
.submit{left:666px;top:2794px;width:107px;height:29px;background:var(--blue);color:var(--white);font-family:"Open Sans",sans-serif;font-weight:700;font-size:14px}
.social{left:1003px;display:flex;align-items:center;gap:12px;font-family:"Open Sans",sans-serif;font-weight:700;font-size:12px;color:var(--white)}
.social i{width:32px;height:32px;border-radius:50%;background:var(--blue-deep);display:block}
.copyright{left:0;top:2875px;width:1200px;height:47px;background:var(--blue);color:var(--white);font-family:"Open Sans",sans-serif;font-weight:600;font-size:13px;line-height:47px;text-align:center}
</style>
</head>
<body>

<!-- header -->
<div class="abs brand"><span class="brand-dot"></span><span class="brand-name">BRAMBLE WORKS</span></div>
<div class="abs top-contact" style="left:736px">
  <span class="round-icon"><svg width="18" height="18" viewBox="0 0 24 24"><path fill="#fff" d="M6.6 10.8c1.4 2.8 3.8 5.1 6.6 6.6l2.2-2.2c.3-.3.7-.4 1-.2 1.1.4 2.3.6 3.6.6.6 0 1 .4 1 1V20c0 .6-.4 1-1 1C10.6 21 3 13.4 3 4c0-.6.4-1 1-1h3.5c.6 0 1 .4 1 1 0 1.3.2 2.5.6 3.6.1.3 0 .7-.2 1z"/></svg></span>
  <span>022 418 3906</span>
</div>
<div class="abs top-contact" style="left:912px">
  <span class="round-icon"><svg width="18" height="14" viewBox="0 0 18 14"><rect x="1" y="1" width="16" height="12" rx="1" fill="none" stroke="#fff" stroke-width="2"/><path d="M1 2l8 6 8-6" fill="none" stroke="#fff" stroke-width="2"/></svg></span>
  <span>Marta.k@bramwks.co.nz</span>
</div>
<div class="abs nav-rule"></div>
<nav class="abs nav">
  <a class="active" style="left:505px">HOME</a>
  <a style="left:608px">ABOUT US</a>
  <a style="left:736px">OUR SERVICES</a>
  <a style="left:900px">PROJECT</a>
  <a style="left:1021px">CONTACT US</a>
</nav>

<!-- hero -->
<div class="abs hero" role="img" aria-label="Photo of a smiling family relaxing on a sofa in a warm, comfortable living room"></div>
<svg class="abs hero-arrow" style="left:62px" width="20" height="36" viewBox="0 0 20 36"><path d="M17 3L4 18l13 15" fill="none" stroke="#fff" stroke-width="3"/></svg>
<svg class="abs hero-arrow" style="left:1120px" width="20" height="36" viewBox="0 0 20 36"><path d="M3 3l13 15L3 33" fill="none" stroke="#fff" stroke-width="3"/></svg>
<div class="abs hero-caption">We have installed thousands of heat pumps and also specialise in diagnostics and repairs</div>

<!-- welcome -->
<h1 class="abs section-title" style="top:686px">WELCOME TO <span>BRAMBLE WORKS</span></h1>
<div class="abs divider" style="top:735px"></div>
<p class="abs welcome-copy">Purchasing a Heatpump or Ventilation System can be a significant investment but it doesnt have to be a daunting one.<br>We have a team of nationally trained and qualified Refrigeration/HVAC and Electricians. We are factory trained and authorised to service and install all major<br>brands including Talvoro, Norvik, Pelnor and Korrowane Electric, Veltrada and Osmelo units. We have installed thousands of heat pumps<br>and also specialise in diagnostics and repairs.</p>
<a class="abs btn btn-primary">Read More <span>»</span></a>

<!-- services -->
<section class="abs services">
  <div class="service light" style="left:0;width:341px">
    <div class="service-bg" role="img" aria-label="Blue-tinted photo of a wall-mounted heat pump"></div>
    <div class="service-icon"><svg width="58" height="40" viewBox="0 0 58 40"><rect x="3" y="3" width="52" height="20" rx="4" fill="none" stroke="#33a6d7" stroke-width="4"/><path d="M16 30c3 3-3 5 0 8M29 30c3 3-3 5 0 8M42 30c3 3-3 5 0 8" fill="none" stroke="#33a6d7" stroke-width="3"/></svg></div>
    <h3>AIR CONDITIONING</h3>
    <p>Heat pumps are the most efficient way of using electricity to heat your home, but some are more efficient</p>
    <a class="btn btn-card">Read More <span>»</span></a>
  </div>
  <div class="service dark" style="left:341px;width:259px">
    <div class="service-bg" role="img" aria-label="Dark-tinted photo of commercial office buildings"></div>
    <div class="service-icon"><svg width="44" height="46" viewBox="0 0 44 46"><rect x="4" y="10" width="22" height="34" fill="none" stroke="#2d4357" stroke-width="4"/><rect x="26" y="20" width="14" height="24" fill="none" stroke="#2d4357" stroke-width="4"/><path d="M10 18h4M16 18h4M10 26h4M16 26h4M10 34h4M16 34h4" stroke="#2d4357" stroke-width="3"/></svg></div>
    <h3>COMMERCIAL</h3>
    <p>We have a growing Portfolio of clients that rely on us for their Commercial requirements. We have proven ourselves to</p>
    <a class="btn btn-card" style="color:var(--navy)">Read More <span>»</span></a>
  </div>
  <div class="service light" style="left:600px;width:257px">
    <div class="service-bg" role="img" aria-label="Blue-tinted photo of a radiator"></div>
    <div class="service-icon"><svg width="46" height="46" viewBox="0 0 46 46"><path d="M12 8c3 3-3 5 0 8M23 8c3 3-3 5 0 8M34 8c3 3-3 5 0 8" fill="none" stroke="#33a6d7" stroke-width="3"/><rect x="6" y="20" width="34" height="20" rx="3" fill="none" stroke="#33a6d7" stroke-width="4"/><path d="M15 20v20M23 20v20M31 20v20" stroke="#33a6d7" stroke-width="3"/></svg></div>
    <h3>CENTRAL HEATING</h3>
    <p>Ducted Heatpumps are the holy grail of central heating and guess what? They can also cool and dehumidify your</p>
    <a class="btn btn-card">Read More <span>»</span></a>
  </div>
  <div class="service dark" style="left:857px;width:343px">
    <div class="service-bg" role="img" aria-label="Dark-tinted photo of a ventilation fan"></div>
    <div class="service-icon"><svg width="50" height="50" viewBox="0 0 50 50"><circle cx="25" cy="25" r="22" fill="none" stroke="#2d4357" stroke-width="4"/><circle cx="25" cy="25" r="4" fill="#2d4357"/><path d="M25 21c-2-8 6-12 8-6zM29 25c8-2 12 6 6 8zM25 29c2 8-6 12-8 6zM21 25c-8 2-12-6-6-8z" fill="#2d4357"/></svg></div>
    <h3>VENTILATION</h3>
    <p>Home ventilation is a very important part of insuring you have a nice dry home to maximise the efficiency of</p>
    <a class="btn btn-card" style="color:var(--navy)">Read More <span>»</span></a>
  </div>
</section>

<!-- gallery -->
<h2 class="abs section-title" style="top:1463px">PROJECT <span>GALLERY</span></h2>
<div class="abs divider" style="top:1514px"></div>
<div class="abs gallery-item" style="left:80px;background:linear-gradient(160deg,#e9e4dd,#b9a997)" role="img" aria-label="Project photo of a bright open-plan living room"></div>
<div class="abs gallery-item" style="left:343px;background:linear-gradient(160deg,#e6e6e6,#b7b7b7)" role="img" aria-label="Project photo of a radiator valve"></div>
<div class="abs gallery-item" style="left:606px;background:linear-gradient(160deg,#d9d4cc,#5b4c40)" role="img" aria-label="Project photo of a bedroom with a heat pump"></div>
<div class="abs gallery-item" style="left:867px;background:linear-gradient(160deg,#f0f0f0,#c4c8cc)" role="img" aria-label="Project photo of a ceiling cassette unit"></div>

<!-- testimonials & why choose -->
<div class="abs band-soft"></div>
<h2 class="abs col-title" style="left:82px">CLIENT <span>TESTIMONIALS</span></h2>
<div class="abs col-rule" style="left:82px;width:480px"></div>
<div class="abs v-dash"></div>
<div class="abs avatar" role="img" aria-label="Portrait photo of the client"></div>
<div class="abs quote-mark">“</div>
<p class="abs quote">Lorem ipsum dolor sit amet, consectetuer adipiscing elit, sed diam nonummy nibh euismod tincidunt ut laoreet dolore magna aliquam erat volutpat. Ut wisi enim ad minim veniam, quis nostrud exerci tation ullamcorper suscipit lobortis nisl ut aliquip</p>
<div class="abs client-name">Hana Ruvell</div>
<div class="abs client-role">Marketing Manager</div>

<h2 class="abs col-title" style="left:649px">WHY CHOOSE <span>BRAMBLE WORKS</span></h2>
<div class="abs col-rule" style="left:649px;width:473px"></div>
<div class="abs why-line"></div>
<div class="abs why-icon" style="top:1923px"><svg width="28" height="28" viewBox="0 0 28 28"><circle cx="14" cy="9" r="6" fill="#fff"/><path d="M3 27c0-7 5-11 11-11s11 4 11 11z" fill="#fff"/></svg></div>
<div class="abs why-icon" style="top:2020px"><svg width="30" height="30" viewBox="0 0 30 30"><circle cx="15" cy="15" r="12" fill="none" stroke="#fff" stroke-width="3"/><path d="M9 15l4 4 8-8" fill="none" stroke="#fff" stroke-width="3"/></svg></div>
<div class="abs why-icon" style="top:2114px"><svg width="30" height="30" viewBox="0 0 30 30"><circle cx="15" cy="15" r="12" fill="none" stroke="#fff" stroke-width="3"/><path d="M9 17c2 4 10 4 12 0" fill="none" stroke="#fff" stroke-width="3"/></svg></div>
<div class="abs why-item" style="top:1934px"><h4>EXPERIENCE COUNTS</h4><p>We have a team of nationally trained and qualified<br>Refrigeration/HVAC/Electrical Engineers and...<a>[+]</a></p></div>
<div class="abs why-sep" style="top:2011px"></div>
<div class="abs why-item" style="top:2030px"><h4>SATISFACTION GUARANTEE</h4><p>We aim to please and I put my name behind our<br>brand! We will take care of your project from...<a>[+]</a></p></div>
<div class="abs why-sep" style="top:2105px"></div>
<div class="abs why-item" style="top:2124px"><h4>LOW PRESSURE SALES</h4><p>Nobody likes the vacuum salesmen’s techniques and<br>neither do we. We will come to your home...<a>[+]</a></p></div>

<!-- brands -->
<h2 class="abs section-title" style="top:2282px">BRANDS WE <span>SERVE</span></h2>
<div class="abs divider" style="top:2330px"></div>
<svg class="abs brand-arrow" style="left:40px" width="16" height="30" viewBox="0 0 16 30"><path d="M14 2L3 15l11 13" fill="none" stroke="#bbb" stroke-width="2"/></svg>
<svg class="abs brand-arrow" style="left:1146px" width="16" height="30" viewBox="0 0 16 30"><path d="M2 2l11 13L2 28" fill="none" stroke="#bbb" stroke-width="2"/></svg>
<div class="abs brand-tile" style="left:80px">Glacewhite</div>
<div class="abs brand-tile" style="left:258px;font-size:15px">Korrowane</div>
<div class="abs brand-tile" style="left:436px">Pelnor</div>
<div class="abs brand-tile" style="left:614px">Veltrada</div>
<div class="abs brand-tile" style="left:791px">Talvoro</div>
<div class="abs brand-tile" style="left:969px">Osmelo</div>

<!-- newsletter -->
<div class="abs newsletter"></div>
<div class="abs news-icon"><svg width="26" height="20" viewBox="0 0 26 20"><rect x="1" y="1" width="24" height="18" rx="2" fill="none" stroke="#fff" stroke-width="2"/><path d="M1 3l12 9 12-9" fill="none" stroke="#fff" stroke-width="2"/></svg></div>
<div class="abs news-title">Sign Up For Newsletter</div>
<div class="abs news-input">Enter your email here</div>
<a class="abs btn news-btn">SUBSCRIBE</a>

<!-- footer -->
<footer class="abs footer"></footer>
<h3 class="abs foot-title" style="left:82px">QUICK <span>LINKS</span></h3>
<div class="abs foot-rule" style="left:82px"></div>
<ul class="abs foot-links">
  <li class="current">Home</li><li>About Us</li><li>Services</li><li>Gallery</li><li>Contact Us</li>
</ul>
<h3 class="abs foot-title" style="left:321px">CONTACT <span>DETAILS</span></h3>
<div class="abs foot-rule" style="left:321px"></div>
<div class="abs foot-contact">
  <strong>BRAMBLE WORKS</strong><br>27 Harlow Crescent Petone, Wellington
  <div class="foot-row"><svg width="14" height="14" viewBox="0 0 24 24"><path fill="#33a6d7" d="M6.6 10.8c1.4 2.8 3.8 5.1 6.6 6.6l2.2-2.2c.3-.3.7-.4 1-.2 1.1.4 2.3.6 3.6.6.6 0 1 .4 1 1V20c0 .6-.4 1-1 1C10.6 21 3 13.4 3 4c0-.6.4-1 1-1h3.5c.6 0 1 .4 1 1 0 1.3.2 2.5.6 3.6.1.3 0 .7-.2 1z"/></svg>022 418 3906</div>
  <div class="foot-row"><svg width="14" height="14" viewBox="0 0 24 24"><path fill="#33a6d7" d="M6.6 10.8c1.4 2.8 3.8 5.1 6.6 6.6l2.2-2.2c.3-.3.7-.4 1-.2 1.1.4 2.3.6 3.6.6.6 0 1 .4 1 1V20c0 .6-.4 1-1 1C10.6 21 3 13.4 3 4c0-.6.4-1 1-1h3.5c.6 0 1 .4 1 1 0 1.3.2 2.5.6 3.6.1.3 0 .7-.2 1z"/></svg>022 418 3906</div>
  <div class="foot-row"><svg width="14" height="11" viewBox="0 0 18 14"><rect x="1" y="1" width="16" height="12" fill="none" stroke="#33a6d7" stroke-width="2"/><path d="M1 2l8 6 8-6" fill="none" stroke="#33a6d7" stroke-width="2"/></svg>Marta.k@bramwks.co.nz</div>
</div>
<h3 class="abs foot-title" style="left:666px">QUICK <span>INQUIRY</span></h3>
<div class="abs foot-rule" style="left:666px"></div>
<div class="abs field" style="top:2680px">Name</div>
<div class="abs field" style="top:2716px">Email</div>
<div class="abs field" style="top:2752px">Message</div>
<a class="abs btn submit">Submit</a>
<h3 class="abs foot-title" style="left:1005px">FOLLOW <span>US</span></h3>
<div class="abs foot-rule" style="left:1005px;width:100px"></div>
<div class="abs social" style="top:2686px"><i></i>FRIENDWALL</div>
<div class="abs social" style="top:2738px"><i style="background:var(--blue)"></i>CHIRPLINE</div>
<div class="abs social" style="top:2791px"><i></i>WORKMESH</div>
<div class="abs copyright">Copyright © 2016 BRAMBLE WORKS. All Rights Reserved.</div>

</body>
</html>
```